LIFE CHANGING NEW WEBSITE DESIGN NEEDED FOR FULL WEBSITE- FUN/FEMININE!

I need a website designed for a personal financial advice website geared at women called BLUE OTTER LANTERN. I will be providing free financial advice around topics of making, saving, spending and sharing money. The concept is to change the way women understand money and the necessity around building various passive income streams to ensure full financial freedom. This will then carry down to advice for mothers with children and children in particular. The website should be elegant and yet witty. I don't want lots of serious photos but more relatable. I will have a photo of myself and my story as this is a blog and needs to be relatable to women and mothers. I like pinks and greys. I want to have a pink piggy bank being broken with a hammer in the front screen to break our traditional mindset around piggy bank saving/spending habits. I have created a logo that is a pink piggy head with BLUE OTTER LANTERN that needs to be incorporated so that it blends into the heading. I have also already started designing the website on Squarespace and can provide access to that. Basically it should have a format of BLUE OTTER LANTERN LOGO center in header then on left hand navigation: MAKE, SAVE, SPEND, SHARE then on right hand header navigation: MISSION, GET STARTED, CONTACT BOL I would like to have the front page when you go to the url to have the image of the piggy bank being broken then a catchy phrase then under 4 boxes with MAKE (image and description) SAVE (image and description) SPEND (image and description) SHARE (image and description) if you click on those or the title they go to pages that are dedicated to each them. Each page should have a little intro on the topic then I want lots of blog links as I will be mainly writing blogs. Each blog site should have ability to write comments as well. I need social media icons on each page too. Please let me know what you need from me to get started. I prefer having a discussion if possible to not waste anyone's time. I need the site to be easy for me to use and add blogs/urls etc as needed. I also need the site to be put into my domain that I already purchased: www.blueotterlantern-sample.com

Target Market(s)

teenage girls, 20 something girls, 30 something girls and mothers

Coding

Coded - Design and coding required

Number of Pages Required

5+ page

Font styles to use
Sans Serif

Colors
e667a6
e34197
f59195
eea4c8
aaaaaa
cbcbcb
959595

Requirements
Must have
• TOP NAVIGATION
• MAKE SAVE SPEND SHARE LOGO/BLUE OTTER LANTERN MISSION GET STARTED CONTACT BOL
• FRONT PAGE: IMAGE OF PIGGY BANK BEING BROKEN WITH A HAMMER
• CATCH PHRASE OVER THE IMAGE
• BUTTON IN PINK- TAKE ACTION (WHICH DIRECTS TO TAKE ACTION TAB ON NAVIGATION HEADER
• 4 BOXES BELOW MAIN IMAGE WITH IMAGE/DESCRIPTIONS FOR MAKE, SAVE, SPEND, SHARE THAT EACH GO TO THE PAGES FROM THE NAVIGATION HEADER
• EACH PAGE SHOULD BE DEDICATED TO THOSE TOPICS THEN THERE IS AN INTRO ON EACH PAGE THEN THE LINKS TO DIFFERENT BLOGS AROUND EACH TOPIC FOR MAKE, SAVE, SPEND, SHARE
• EACH BLOG SHOULD HAVE COMMENTS SECTION AND SOCIAL MEDIA ICONS
• (GOOD TO USE PINKS/GREYS)
Should not have
• BE SUPER BUSY, CLUTTERED, FEEL LIKE I AM SELLING SOMETHING

```html
<!DOCTYPE html>
<html lang="en">
<head>
<meta charset="utf-8">
<title>Blue Otter Lantern</title>
<link href="https://fonts.googleapis.com/css2?family=Quicksand:wght@500;600;700&family=Roboto:wght@400;500;700&display=swap" rel="stylesheet">
<style>
:root{
  --pink:#e0197d;
  --pink-soft:#e34197;
  --pink-light:#eea4c8;
  --ink:#1d1d1d;
  --text:#555;
  --grey:#959595;
  --grey-light:#cbcbcb;
  --mist:#eef0f4;
  --dark:#2a2828;
  --white:#fff;
}
*{box-sizing:border-box;margin:0;padding:0}
html,body{width:1200px;height:3349px;overflow:hidden;background:var(--white)}
body{position:relative;font-family:'Roboto',sans-serif;color:var(--text)}
.abs{position:absolute}
.center{left:0;width:1200px;text-align:center}
.heading{font-family:'Quicksand',sans-serif;font-weight:600;color:var(--ink);font-size:43px}

/* header */
.topline{top:0;left:0;width:1200px;height:3px;background:var(--pink)}
.header{top:3px;left:0;width:1200px;height:110px;background:var(--white);z-index:5}
.nav{top:48px;display:flex;gap:21px;font-size:16px;font-weight:500;color:var(--ink);letter-spacing:.2px}
.nav.left{left:110px}
.nav.right{right:111px}
.brand-cap{left:470px;top:60px;width:260px;height:80px;border-radius:0 0 130px 130px/0 0 80px 80px;background:var(--white);z-index:4}
.brand{left:430px;top:16px;width:340px;text-align:center;z-index:6}
.brand-mark{width:44px;height:44px;border:3px solid var(--pink-soft);border-radius:50%;margin:0 auto 4px}
.brand-name{font-family:'Quicksand',sans-serif;font-weight:600;color:var(--pink-soft);font-size:27px}

/* hero */
.hero{top:113px;left:0;width:1200px;height:615px;overflow:hidden}
.hero-photo{position:absolute;inset:0;background:radial-gradient(ellipse at 55% 45%,#c04a5c 0%,#8f4a3b 28%,#6d5544 55%,#4e4035 100%)}
.hero-title{top:200px;font-family:'Quicksand',sans-serif;font-weight:700;color:var(--white);font-size:68px;text-shadow:0 3px 8px rgba(0,0,0,.45)}
.hero-sub{top:290px;color:var(--white);font-size:20px;font-weight:500;line-height:31px;text-shadow:0 2px 5px rgba(0,0,0,.6)}
.btn-hero{top:371px;left:494px;width:212px;height:50px;border:2px solid var(--white);border-radius:25px;background:var(--pink);color:var(--white);font-weight:700;font-size:19px;display:flex;align-items:center;justify-content:center;gap:6px}
.hero-curve{left:0;top:488px}

/* intro */
.intro-title{top:805px}
.intro-text{top:874px;font-size:15px;line-height:30px;color:var(--text)}
.pillar{top:975px;width:221px;height:375px;background:var(--white);box-shadow:0 0 6px rgba(0,0,0,.15);text-align:center}
.pillar-photo{margin:4px;height:175px}
.pillar-icon{position:absolute;left:74px;top:143px;width:72px;height:72px;border-radius:50%;background:var(--white);display:flex;align-items:center;justify-content:center}
.pillar h3{margin-top:30px;font-size:25px;font-weight:700;color:var(--ink)}
.pillar p{margin-top:8px;font-size:15px;line-height:27px;color:var(--text);padding:0 8px}
.pillar .go{margin-top:12px}

/* stories */
.stories{top:1426px;left:0;width:1200px;height:714px;background:linear-gradient(180deg,#eceef2 0%,#f3f4f7 50%,#e7e9ee 100%)}
.stories-label{top:1568px;color:var(--pink);font-size:18px}
.stories-title{top:1605px}
.portrait{left:147px;top:1699px;width:281px;height:281px;border-radius:50%;border:4px solid var(--white);background:linear-gradient(160deg,#8c6e5c,#5d4639 55%,#6a86a8);box-shadow:0 2px 10px rgba(0,0,0,.15)}
.quote{left:484px;top:1699px;width:584px;height:207px;background:var(--white);box-shadow:0 1px 6px rgba(0,0,0,.12);padding:22px 26px}
.quote-tail{left:484px;top:1904px}
.quote h4{font-family:'Quicksand',sans-serif;font-weight:600;color:var(--pink);font-size:22px}
.quote p{margin-top:12px;font-size:15px;line-height:27px;color:var(--text)}
.watch{margin-top:10px;display:flex;align-items:center;gap:10px;color:var(--pink);font-size:15px}
.watch i{width:35px;height:35px;border-radius:50%;background:var(--pink);display:flex;align-items:center;justify-content:center}
.client{left:486px;top:1948px;display:flex;align-items:center;gap:16px;font-size:15px}
.client-co{display:flex;align-items:center;gap:6px;color:#3c8f3c;font-size:13px}
.client-co span{width:12px;height:12px;background:#7ab443}
.client b{color:var(--pink);font-size:18px;font-weight:500}
.stories-edge{left:0}

/* blog */
.blog-title{top:2188px}
.blog-sub{top:2257px;font-size:15px;color:#333}
.post{top:2308px;width:303px;height:414px;background:var(--white);box-shadow:0 0 6px rgba(0,0,0,.15);border-bottom:3px solid var(--pink-light)}
.post-photo{margin:3px;height:184px;position:relative}
.post-date{position:absolute;left:20px;bottom:12px;background:var(--pink-soft);color:var(--white);font-size:13px;padding:4px 9px}
.post-body{padding:20px 16px 0 18px;position:relative}
.post-body:before{content:"";position:absolute;left:0;top:22px;width:3px;height:42px;background:var(--pink-light)}
.post h5{font-size:19px;font-weight:500;color:var(--ink)}
.post-meta{margin-top:12px;font-size:13px;color:var(--grey);display:flex;gap:10px;align-items:center}
.post-meta i{width:9px;height:9px;background:var(--pink);border-radius:50%;display:inline-block;margin-right:5px}
.post p{margin-top:20px;font-size:14px;line-height:25px;color:var(--text);text-align:justify}
.read{margin-top:12px;color:var(--pink);font-weight:700;font-size:14px}

/* footer */
.footer{top:2820px;left:0;width:1200px;height:529px}
.footer-body{position:absolute;top:148px;left:0;width:1200px;height:381px;background:var(--dark)}
.foot-brand{left:430px;top:2900px;width:340px;text-align:center}
.foot-brand .brand-mark{width:40px;height:40px}
.join{left:112px;top:3006px;color:var(--white);font-family:'Quicksand',sans-serif;font-weight:700;font-size:26px;line-height:36px}
.subscribe{left:602px;top:3018px;display:flex}
.subscribe .field{width:340px;height:46px;background:var(--white);color:#666;font-size:15px;padding:14px 18px}
.subscribe .send{width:147px;height:46px;background:var(--pink);color:var(--white);font-weight:500;font-size:16px;display:flex;align-items:center;justify-content:center}
.rule{top:3164px;height:1px;background:#777}
.social{left:485px;top:3141px;display:flex;gap:16px}
.social span{width:46px;height:46px;border:2px solid var(--white);border-radius:50%;color:var(--white);font-size:10px;display:flex;align-items:center;justify-content:center}
.foot-links{top:3232px;color:var(--white);font-size:15px;word-spacing:2px}
.foot-links em{font-style:normal;margin:0 14px}
.copy{top:3272px;color:var(--white);font-size:15px}
</style>
</head>
<body>

<div class="abs topline"></div>
<header class="abs header">
  <nav class="abs nav left"><span>HOME</span><span>MAKE</span><span>SAVE</span><span>SPEND</span><span>SHARE</span></nav>
  <nav class="abs nav right"><span>MISSION</span><span>GET STARTED</span><span>CONTACT BOL</span></nav>
</header>
<div class="abs brand-cap"></div>
<div class="abs brand"><div class="brand-mark"></div><div class="brand-name">Blue Otter Lantern</div></div>

<section class="abs hero">
  <div class="hero-photo" role="img" aria-label="Pink piggy bank broken by a hammer among scattered coins on a wooden table"></div>
  <h1 class="abs center hero-title">Blue Otter Lantern</h1>
  <p class="abs center hero-sub">To rethink the way you think about growing, spending<br>and saving money.</p>
  <div class="abs btn-hero">READ MORE
    <svg width="17" height="17" viewBox="0 0 16 16"><circle cx="8" cy="8" r="8" fill="#fff"/><path d="M6 4.5 9.5 8 6 11.5" stroke="#e0197d" stroke-width="2.2" fill="none"/></svg></div>
  <svg class="abs hero-curve" width="1200" height="140" viewBox="0 0 1200 140">
    <path d="M0 10 Q600 206 1200 10 V140 H0Z" fill="#fff"/>
    <path d="M40 28 Q600 226 1160 28 Q600 190 40 28Z" fill="#e0197d"/>
  </svg>
</section>

<h2 class="abs center heading intro-title">Blue Otter Lantern</h2>
<p class="abs center intro-text">Lorem ipsum dolor sit amet, consectetur adipiscing elit, sed do eiusmod tempor incididunt ut labore<br>et dolore magna aliqua. Ut enim ad minim veniam, quis nostrud.</p>

<article class="abs pillar" style="left:112px">
  <div class="pillar-photo" role="img" aria-label="Hand holding a fan of banknotes" style="background:linear-gradient(135deg,#9a7a62,#6f8f6a 60%,#c8a070)"></div>
  <div class="pillar-icon"><svg width="40" height="40" viewBox="0 0 40 40" fill="none" stroke="#e0197d" stroke-width="2"><circle cx="20" cy="20" r="14"/><path d="M20 12v16M24 15h-6a3 3 0 0 0 0 6h4a3 3 0 0 1 0 6h-6"/></svg></div>
  <h3>MAKE</h3>
  <p>Lorem ipsum dolor sit consectetur adipiscing elsed do eiusmod tempor.</p>
  <svg class="go" width="20" height="20" viewBox="0 0 16 16"><circle cx="8" cy="8" r="8" fill="#e0197d"/><path d="M4.5 6.5 8 10l3.5-3.5" stroke="#fff" stroke-width="2.2" fill="none"/></svg>
</article>
<article class="abs pillar" style="left:364px">
  <div class="pillar-photo" role="img" aria-label="Hand dropping a coin into a pink piggy bank" style="background:linear-gradient(135deg,#c9a793,#e8cfc6 55%,#a8887a)"></div>
  <div class="pillar-icon"><svg width="40" height="40" viewBox="0 0 40 40" fill="none" stroke="#e0197d" stroke-width="2"><circle cx="20" cy="20" r="14"/><path d="M20 12v16M24 15h-6a3 3 0 0 0 0 6h4a3 3 0 0 1 0 6h-6"/></svg></div>
  <h3>SAVE</h3>
  <p>Lorem ipsum dolor sit consectetur adipiscing elsed do eiusmod tempor.</p>
  <svg class="go" width="20" height="20" viewBox="0 0 16 16"><circle cx="8" cy="8" r="8" fill="#e0197d"/><path d="M4.5 6.5 8 10l3.5-3.5" stroke="#fff" stroke-width="2.2" fill="none"/></svg>
</article>
<article class="abs pillar" style="left:615px">
  <div class="pillar-photo" role="img" aria-label="Hourglass standing on a spread of coins" style="background:linear-gradient(135deg,#5d86b8,#9fb7d2 45%,#6e6658)"></div>
  <div class="pillar-icon"><svg width="40" height="40" viewBox="0 0 40 40" fill="none" stroke="#e0197d" stroke-width="2"><circle cx="20" cy="20" r="14"/><path d="M20 12v16M24 15h-6a3 3 0 0 0 0 6h4a3 3 0 0 1 0 6h-6"/></svg></div>
  <h3>SPEND</h3>
  <p>Lorem ipsum dolor sit consectetur adipiscing elsed do eiusmod tempor.</p>
  <svg class="go" width="20" height="20" viewBox="0 0 16 16"><circle cx="8" cy="8" r="8" fill="#e0197d"/><path d="M4.5 6.5 8 10l3.5-3.5" stroke="#fff" stroke-width="2.2" fill="none"/></svg>
</article>
<article class="abs pillar" style="left:867px">
  <div class="pillar-photo" role="img" aria-label="Banknotes being passed from one hand to another" style="background:linear-gradient(135deg,#8a4b24,#c99a72 50%,#5a6f9a)"></div>
  <div class="pillar-icon"><svg width="40" height="40" viewBox="0 0 40 40" fill="none" stroke="#e0197d" stroke-width="2"><circle cx="13" cy="20" r="6"/><circle cx="28" cy="11" r="6"/><circle cx="28" cy="29" r="6"/><path d="M18 18l5-4M18 22l5 4"/></svg></div>
  <h3>SHARE</h3>
  <p>Lorem ipsum dolor sit consectetur adipiscing elsed do eiusmod tempor.</p>
  <svg class="go" width="20" height="20" viewBox="0 0 16 16"><circle cx="8" cy="8" r="8" fill="#e0197d"/><path d="M4.5 6.5 8 10l3.5-3.5" stroke="#fff" stroke-width="2.2" fill="none"/></svg>
</article>

<section class="abs stories" role="img" aria-label="Soft faded background of a white piggy bank and stacked coins">
  <svg class="abs stories-edge" style="top:0" width="1200" height="62" viewBox="0 0 1200 62"><path d="M0 0 H1200 Q600 120 0 0Z" fill="#fff"/></svg>
  <svg class="abs stories-edge" style="bottom:0" width="1200" height="60" viewBox="0 0 1200 60"><path d="M0 60 Q600 -50 1200 60Z" fill="#fff"/></svg>
</section>
<p class="abs center stories-label">CUSTOMERS</p>
<h2 class="abs center heading stories-title">Customer Success Stories</h2>
<div class="abs portrait" role="img" aria-label="Portrait of a smiling client"></div>
<div class="abs quote">
  <h4>Lorem Ipsum</h4>
  <p>Lorem ipsum dolor sit amet, consectetur adipiscing elit, sed do eiusmod tempor incididunt ut labore et dolore magna aliqua. Quis ipsum suspendisse ultrices gravida. Risus commodo viverra maecenas.</p>
  <div class="watch"><i><svg width="14" height="14" viewBox="0 0 14 14"><path d="M4 2l8 5-8 5z" fill="#fff"/></svg></i>Watch the Story</div>
</div>
<svg class="abs quote-tail" width="18" height="24" viewBox="0 0 18 24"><path d="M0 0H18L0 24Z" fill="#fff"/></svg>
<div class="abs client">
  <div class="client-co"><span></span>Fernbrook Co</div>
  <div><b>Client Name,</b> Lorem ipsum dolor sit amet</div>
</div>

<h2 class="abs center heading blog-title">From The Blog</h2>
<p class="abs center blog-sub">Lorem ipsum dolor sit amet, consectetur adipiscing elit sed do eiusmod tempor.</p>

<article class="abs post" style="left:112px">
  <div class="post-photo" role="img" aria-label="Piggy bank in sunglasses on a sunny beach" style="background:linear-gradient(180deg,#4ea3dd,#9bd0ec 45%,#e7d2a8)"><span class="post-date">JUNE 16, 2019</span></div>
  <div class="post-body">
    <h5>Minus quod maxime placeat</h5>
    <div class="post-meta"><span><i></i>Mara Quill</span>|<span>25 comments</span></div>
    <p>Lorem ipsum dolor sit amet, consectetur adipiscing elit, sed do eiusmod tempor incididunt ut labore...</p>
    <div class="read">Read More ›</div>
  </div>
</article>
<article class="abs post" style="left:449px">
  <div class="post-photo" role="img" aria-label="Hand stacking coins in front of a world map" style="background:linear-gradient(135deg,#2f5d92,#a7c4e4 55%,#e8eef6)"><span class="post-date">JUNE 16, 2019</span></div>
  <div class="post-body">
    <h5>Minus quod maxime placeat</h5>
    <div class="post-meta"><span><i></i>Mara Quill</span>|<span>25 comments</span></div>
    <p>Lorem ipsum dolor sit amet, consectetur adipiscing elit, sed do eiusmod tempor incididunt ut labore...</p>
    <div class="read">Read More ›</div>
  </div>
</article>
<article class="abs post" style="left:786px">
  <div class="post-photo" role="img" aria-label="Coloured pie chart pieces with coins on a wooden table" style="background:linear-gradient(135deg,#5a3a2a,#7a4d35 50%,#3e2a20)"><span class="post-date">JUNE 16, 2019</span></div>
  <div class="post-body">
    <h5>Minus quod maxime placeat</h5>
    <div class="post-meta"><span><i></i>Mara Quill</span>|<span>25 comments</span></div>
    <p>Lorem ipsum dolor sit amet, consectetur adipiscing elit, sed do eiusmod tempor incididunt ut labore...</p>
    <div class="read">Read More ›</div>
  </div>
</article>

<footer class="abs footer">
  <svg class="abs" style="top:0;left:0" width="1200" height="152" viewBox="0 0 1200 152">
    <path d="M0 152 Q600 -90 1200 152Z" fill="#2a2828"/>
    <path d="M50 122 Q600 -92 1150 122 Q600 -62 50 122Z" fill="#e0197d"/>
  </svg>
  <div class="footer-body"></div>
</footer>
<div class="abs foot-brand"><div class="brand-mark"></div><div class="brand-name">Blue Otter Lantern</div></div>
<div class="abs join">WANT TO KNOW ABOUT US<br>JOIN THE COMMUNITY</div>
<div class="abs subscribe"><div class="field">Email Address</div><div class="send">SUBSCRIBE</div></div>
<div class="abs rule" style="left:112px;width:352px"></div>
<div class="abs rule" style="left:737px;width:352px"></div>
<div class="abs social"><span>Feed</span><span>Chat</span><span>Pics</span><span>Video</span></div>
<p class="abs center foot-links">Home<em>|</em>Make<em>|</em>Save<em>|</em>Spend<em>|</em>Share<em>|</em>Mission<em>|</em>Get Started<em>|</em>Blog<em>|</em>Contact Us</p>
<p class="abs center copy">Copyright © 2019 Blue Otter Lantern. All Rights Reserved.</p>

</body>
</html>
```